Business card

We need a business card design for our company based in Auckland , New Zealand called 'Ridge + Studio Ltd'. We provide architectural services. We would like to see designs that use the max. three colours (such as white, black, grey) The final design should communicate financial safety and growth."
Also I will provide our company logo. I would like to the logo to be embeded onto our business card.

Target Market(s)

new residential house, alteration & addition & light commericila design & drafting service

Industry/Entity Type

Architecture

Contact Information for Business Card

Company name: ridge + studio Ltd.
Name: Mark Delford
Job title: architectural designer & Design LBP
email address: mark@rplusd.co.nz
mobile number: 02 5163 2290
web site: www.rplusd.co.nz

Requirements
Must have
• My project must have..
• - embeded logo (attached company logo)
• I don't have a bigger version for our company logo, but I have one old one, so you can remove the word from it)
• - insert the attached small BKTW logo & LBP logo
• - creative, simple and clear business card.
• - Max. three colours
Nice to have
• - Here are the samples I would like to share with you: http://www.plimvora.com/blog/minimalistic-business-card-designs/
• I would like to have my business card like one of the creation.
Should not have
• TBA

```html
<!DOCTYPE html>
<html lang="en">
<head>
<meta charset="utf-8">
<title>Ridge + Studio Ltd – Business Card</title>
<link href="https://fonts.googleapis.com/css2?family=Open+Sans:wght@400;600;700;800&display=swap" rel="stylesheet">
<style>
  :root {
    --backdrop: #3c3c3c;
    --card-light: #ffffff;
    --card-dark: #000000;
    --ink: #111111;
    --ink-muted: #8a9091;
    --ink-body: #333333;
    --ink-inverse: #ffffff;
  }
  * { box-sizing: border-box; margin: 0; padding: 0; }
  html, body {
    width: 1105px; height: 1200px; overflow: hidden;
    background: var(--backdrop);
    font-family: "Open Sans", Arial, sans-serif;
  }
  .canvas { position: relative; width: 1105px; height: 1200px; }
  .card { position: absolute; left: 193px; width: 720px; height: 410px; }
  .card--front { top: 167px; background: var(--card-light); color: var(--ink); }
  .card--back { top: 623px; background: var(--card-dark); color: var(--ink-inverse); }

  .person { position: absolute; left: 46px; top: 150px; }
  .person__name { font-size: 23px; font-weight: 700; letter-spacing: 0.3px; line-height: 1.2; }
  .person__role { margin-top: 4px; font-size: 17px; color: var(--ink-muted); line-height: 1.6; }
  .person__company { margin-top: 16px; font-size: 18px; color: var(--ink-body); }
  .contact { list-style: none; margin-top: 10px; }
  .contact__item { display: flex; align-items: center; gap: 10px; font-size: 17px; color: var(--ink-body); height: 28px; }
  .contact__icon { width: 18px; height: 18px; flex: none; }

  .brand { position: absolute; left: 318px; top: 15px; width: 390px; height: 380px;
    display: flex; align-items: center; justify-content: center; gap: 14px; }
  .brand__dot { width: 22px; height: 22px; border-radius: 50%; background: var(--ink); }
  .brand__name { font-size: 30px; font-weight: 700; color: var(--ink); letter-spacing: 0.5px; }

  .badge { position: absolute; left: 112px; top: 95px; width: 182px; height: 182px;
    border-radius: 50%; background: var(--ink-inverse); }
  .divider { position: absolute; left: 326px; top: 95px; width: 1px; height: 220px; background: var(--ink-inverse); }
  .partner { position: absolute; left: 345px; top: 140px; font-size: 82px; font-weight: 800;
    line-height: 1; letter-spacing: -2px; color: var(--ink-inverse); }
  .back-web { position: absolute; left: 0; right: 0; top: 343px; text-align: center;
    font-size: 19px; color: var(--ink-inverse); }
</style>
</head>
<body>
<main class="canvas">
  <section class="card card--front" aria-label="Card front">
    <div class="person">
      <h1 class="person__name">MARK DELFORD</h1>
      <p class="person__role">architectural designer<br>&amp; Design LBP</p>
      <p class="person__company">Ridge + Studio Ltd.</p>
      <ul class="contact">
        <li class="contact__item">
          <svg class="contact__icon" viewBox="0 0 18 18"><rect x="4" y="1" width="10" height="16" rx="2" fill="none" stroke="#111" stroke-width="2"/><rect x="8" y="13" width="2" height="2" fill="#111"/></svg>
          02 5163 2290
        </li>
        <li class="contact__item">
          <svg class="contact__icon" viewBox="0 0 18 18"><rect x="1" y="4" width="16" height="11" fill="#111"/><path d="M1 4 L9 11 L17 4" fill="none" stroke="#fff" stroke-width="1.5"/></svg>
          mark@rplusd.co.nz
        </li>
        <li class="contact__item">
          <svg class="contact__icon" viewBox="0 0 18 18"><circle cx="9" cy="9" r="8" fill="#111"/><path d="M5 6 Q8 5 9 8 Q8 11 6 11 Z M11 10 Q13 9 14 12 Q12 14 11 12 Z" fill="#fff"/></svg>
          www.rplusd.co.nz
        </li>
      </ul>
    </div>
    <div class="brand">
      <span class="brand__dot"></span>
      <span class="brand__name">Ridge + Studio</span>
    </div>
  </section>

  <section class="card card--back" aria-label="Card back">
    <div class="badge" role="img" aria-label="Partner certification badge"></div>
    <div class="divider"></div>
    <p class="partner">BKTW</p>
    <p class="back-web">www.rplusd.co.nz</p>
  </section>
</main>
</body>
</html>
```